Meridale Bed Company Needs Business Card

Looking for a very nice looking business card. Creative but not extravagant. We sell beds and pillows across the U.S. and need something professional but catchy. I have attached the logo.

Name : Devin Holt
Title : President
Phone : (800) 471-2960
Email: sleep@quilmora.com
Website: www.quilmora.com

Can be single-sided or double-sided
horizontal or vertical

Can use Blues/Greys

Target Market(s)

Mass Market

Industry/Entity Type

Retail

Contact Information for Business Card

Name : Devin Holt
Title : President
Phone : (800) 471-2960
Email: sleep@quilmora.com
Website: www.quilmora.com

Requirements
Must have
• Clean, Modern, Smooth
• Can use Blues/Greys
• On the other side without the information - have something simple like www.quilmora.com or our logo
Nice to have
• Surprise me
Should not have
• Nothing crazy, nothing cluttered

```html
<!DOCTYPE html>
<html lang="en">
<head>
<meta charset="utf-8">
<title>Meridale Bed Company – Business Card</title>
<link href="https://fonts.googleapis.com/css2?family=Quicksand:wght@300&family=Arimo:wght@400;700&display=swap" rel="stylesheet">
<style>
  :root {
    --backdrop: #e6e4e1;
    --card: #3b3b3c;
    --card-edge: #2e2e2f;
    --silver: #8d8d8f;
    --brand-blue: #2aa5e2;
    --ink-light: #f2f2f2;
    --divider: #d9d9d9;
  }
  * { margin: 0; padding: 0; box-sizing: border-box; }
  html, body { width: 1200px; height: 769px; overflow: hidden; }
  body {
    background: var(--backdrop);
    position: relative;
    font-family: "Arimo", Arial, sans-serif;
  }
  .card {
    position: absolute;
    top: 236px;
    width: 520px;
    height: 297px;
    background: var(--card);
    border: 1px solid var(--card-edge);
  }
  .card--front { left: 50px; }
  .card--back { left: 630px; }

  .wordmark {
    position: absolute;
    font-family: "Quicksand", "Helvetica Neue", sans-serif;
    font-weight: 300;
    letter-spacing: 1px;
    line-height: 1;
    white-space: nowrap;
  }
  .card--front .wordmark {
    color: var(--silver);
    font-size: 92px;
    left: 50%;
    top: 50%;
    transform: translate(-50%, -58%);
  }
  .card--back .wordmark {
    color: var(--brand-blue);
    font-size: 84px;
    left: 108px;
    top: 50px;
  }

  .person {
    position: absolute;
    right: 310px;
    top: 178px;
    text-align: right;
  }
  .person__name {
    color: var(--brand-blue);
    font-weight: 700;
    font-size: 19px;
    line-height: 24px;
  }
  .person__title {
    color: var(--ink-light);
    font-size: 16px;
    line-height: 22px;
  }
  .divider {
    position: absolute;
    left: 226px;
    top: 178px;
    width: 1px;
    height: 76px;
    background: var(--divider);
  }
  .contacts {
    position: absolute;
    left: 242px;
    top: 180px;
    list-style: none;
  }
  .contacts__item {
    display: flex;
    align-items: center;
    gap: 8px;
    color: var(--ink-light);
    font-size: 14.5px;
    line-height: 24px;
  }
  .contacts__icon { width: 13px; height: 13px; fill: var(--brand-blue); flex: none; }
</style>
</head>
<body>
  <section class="card card--front" aria-label="Card front">
    <div class="wordmark">quilmora</div>
  </section>

  <section class="card card--back" aria-label="Card back">
    <div class="wordmark">quilmora</div>

    <div class="person">
      <p class="person__name">Devin Holt</p>
      <p class="person__title">President</p>
    </div>

    <div class="divider"></div>

    <ul class="contacts">
      <li class="contacts__item">
        <svg class="contacts__icon" viewBox="0 0 16 16" aria-hidden="true">
          <path d="M1 5c0-2 3-3 7-3s7 1 7 3v1h-3.5V4.5h-7V6H1z"/>
          <path d="M4 7h8l2 7H2z"/>
        </svg>
        (800) 471-2960
      </li>
      <li class="contacts__item">
        <svg class="contacts__icon" viewBox="0 0 16 16" aria-hidden="true">
          <path d="M1 3h14v1.5L8 9 1 4.5z"/>
          <path d="M1 6.3l7 4.5 7-4.5V13H1z"/>
        </svg>
        sleep@quilmora.com
      </li>
      <li class="contacts__item">
        <svg class="contacts__icon" viewBox="0 0 16 16" aria-hidden="true">
          <circle cx="8" cy="8" r="7"/>
          <path d="M8 1.5v13M1.5 8h13" stroke="#3b3b3c" stroke-width="1.2" fill="none"/>
        </svg>
        www.quilmora.com
      </li>
    </ul>
  </section>
</body>
</html>
```